Exciting opportunity to create logo and a label for our natural health brand.

About us

We are a customer centric health supplement brand who believes in natural medicine and high quality ingredients. We take a holistic approach to healthcare, with an eastern philosophy. We believe in being partners with our customers in their health care journey and are invested in their well being.

Our brand philosophy and values are attached (see Vorna philosophy.png). Our personality traits are:

- Natural
- Fresh
- Modern
- Balanced (in a holistic sense)

Task breakdown

1. Design a fresh feeling logo for us
- We want it to represent our values and high quality ingredients. We would like the quality of the product to be reflected in the branding and have a high end feel.
- Logo text must include Vorna Health Sciences
- We want the Vorna to be the focus of the logo (see uploaded image Vorna logo example.png)
The logo does not have to follow this layout, but we just want the Vorna to stand out. Feel free to use your creative license on this!

2. Create an attractive label to go on the supplement bottle
- The designs need to be eye catching, give a sense of high end ingredients and natural products and tie in with the logo to give a joined up feel.
- We are selling our products online and need them to really stand out from the competition.
- See examples of labels and packaging we like (1 -7 label design).

The initial label we would like you to design would be for our product Calm Drift. It is a product that assists in the management of Anxiety and stress. The label will appear on the bottle that holds the capsules for this supplement, see uploaded files (Example plain bottles.png). The bottles may be white as the picture shows or dark blue recyclable plastic or dark brown glass . We don't have the exact dimensions of the bottle yet, but I will follow up with these.

The label needs to include the following things:
1. The logo
2. The name of the product
3. The product is to help with the relief of Anxiety and Stress
4. Number of capsules the bottle contains
5. The back of the label should have
i) The ingredients
ii) Dosage
iii) Directions of use

Please use placeholder text where needed.

We look forward to seeing your design. Thank you.

```html
<!DOCTYPE html>
<html lang="en">
<head>
<meta charset="utf-8">
<title>Calm Drift – Vorna Health Sciences Label</title>
<link rel="stylesheet" href="https://fonts.googleapis.com/css2?family=Bebas+Neue&family=Poppins:wght@400;600&family=Roboto+Condensed:wght@400;700&family=Yellowtail&display=swap">
<style>
  :root {
    --page: #ffffff;
    --label: #dfe7d1;
    --green: #37663f;
    --ink: #222222;
    --disclaimer: #c3d1b7;
    --white: #ffffff;
    --bloom-light: rgba(255,255,255,0.6);
    --bloom-green: rgba(120,170,100,0.35);
  }
  * { margin: 0; padding: 0; box-sizing: border-box; }
  html, body { width: 1200px; height: 1200px; overflow: hidden; background: var(--page); }
  .canvas { position: relative; width: 1200px; height: 1200px; }
  .label {
    position: absolute; left: 0; top: 358px; width: 1200px; height: 485px;
    background: var(--label); border-radius: 12px; overflow: hidden;
    font-family: "Roboto Condensed", sans-serif; color: var(--ink);
  }
  .abs { position: absolute; }
  .lines { white-space: nowrap; }

  /* left panel */
  .info { left: 16px; font-size: 14.6px; line-height: 17.7px; }
  .info b { color: var(--green); font-weight: 700; letter-spacing: 0.4px; }
  .usage { top: 16px; }
  .warning { top: 82px; }
  .rule { height: 2px; background: var(--green); }
  .rule-top { left: 15px; top: 269px; width: 272px; }
  .rule-bottom { left: 16px; top: 352px; width: 272px; }
  .caution {
    left: 17px; top: 277px; font-size: 14.2px; line-height: 17.7px;
    color: var(--green); letter-spacing: 0.6px;
  }
  .disclaimer {
    left: 17px; top: 361px; width: 266px; height: 61px; background: var(--disclaimer);
    padding: 4px 6px; font-size: 14.4px; line-height: 17.7px;
  }

  /* centre panel */
  .brand { left: 427px; top: 38px; color: var(--ink); font-family: "Roboto Condensed", sans-serif; font-weight: 700; }
  .brand-name { font-size: 54px; line-height: 56px; letter-spacing: 1px; }
  .brand-sub { font-size: 13px; line-height: 16px; letter-spacing: 0.8px; margin-top: 2px; padding-left: 2px; }
  .product {
    left: 424px; top: 226px; font-family: "Bebas Neue", sans-serif; font-weight: 400;
    font-size: 66px; line-height: 66px; letter-spacing: 0.5px; color: var(--ink);
  }
  .bar { height: 4px; background: var(--green); }
  .bar-a { left: 425px; top: 298px; width: 138px; }
  .bar-b { left: 428px; top: 379px; width: 138px; }
  .claim {
    left: 429px; top: 313px; font-family: "Poppins", sans-serif; font-weight: 400;
    font-size: 18px; line-height: 24px; letter-spacing: 2px; color: var(--ink); z-index: 2;
  }
  .claim strong { font-weight: 600; }
  .tagline {
    left: 428px; top: 397px; font-family: "Yellowtail", cursive; font-size: 21px;
    line-height: 28px; color: var(--ink); z-index: 2; white-space: nowrap;
  }
  .bloom {
    left: 604px; top: 322px; width: 172px; height: 126px; border-radius: 50% 50% 40% 40%;
    background: radial-gradient(ellipse at 50% 70%, var(--bloom-light), var(--bloom-green) 50%, rgba(223,231,209,0) 72%);
  }

  /* right panel */
  .facts {
    left: 920px; top: 14px; width: 253px; height: 234px; border: 2.5px solid var(--ink);
    background: var(--white); text-align: center; font-weight: 700; font-size: 14px;
    letter-spacing: 0.6px; padding-top: 10px;
  }
  .ingredients { left: 920px; top: 264px; font-size: 14.6px; line-height: 18.5px; }
  .ingredients b, .maker b { font-weight: 700; letter-spacing: 0.5px; }
  .maker { left: 920px; top: 317px; font-size: 14.6px; line-height: 18.5px; letter-spacing: 0.6px; }
  .code-box {
    left: 921px; top: 370px; width: 255px; height: 67px; background: var(--white);
    display: flex; align-items: center; justify-content: center; font-size: 14px; letter-spacing: 0.3px;
  }

  /* footer band */
  .band {
    left: 0; top: 443px; width: 1200px; height: 36px; background: var(--green); color: var(--white);
  }
  .band-url { top: 0; line-height: 36px; font-size: 14.6px; transform: translateX(-50%); white-space: nowrap; }
  .band-left { left: 153px; }
  .band-right { left: 1043px; }
  .band-center {
    left: 427px; top: 0; line-height: 36px; font-family: "Poppins", sans-serif;
    font-size: 16.5px; letter-spacing: 2.2px; white-space: nowrap;
  }
</style>
</head>
<body>
<div class="canvas">
  <section class="label">
    <p class="abs info usage lines"><b>SUGGESTED USE:</b> As a dietary supplement,<br>take one capsule twice daily, preferably with<br>meals.</p>
    <p class="abs info warning lines"><b>WARNING:</b> If you are pregnant or<br>breastfeeding, do not use this product. If<br>symptoms persist or worsen, or if new<br>symptoms develop, discontinue use and<br>consult a health care practitioner. If you are<br>taking prescription medications, consult a<br>health care practitioner prior to use.<br>Consumption with alcohol, other drugs or<br>natural health products with sedative<br>properties is not recommend</p>
    <div class="abs rule rule-top"></div>
    <p class="abs caution lines">KEEP OUT OF REACH OF CHILDREN.<br>DO NOT USE IF SAFETY SEAL IS<br>DAMAGED OR MISSING. STORE IA A<br>COOL, DRY PLACE.</p>
    <div class="abs rule rule-bottom"></div>
    <p class="abs disclaimer lines">These products have not been evaluated by<br>the FDA and are not intended to diagnose,<br>treat, cure, or prevent any disease.</p>

    <div class="abs brand">
      <div class="brand-name">VORNA</div>
      <div class="brand-sub">HEALTH SCIENCES</div>
    </div>

    <div class="abs bloom" role="img" aria-label="Soft lotus flower decoration in pale green"></div>
    <h1 class="abs product">CALM DRIFT</h1>
    <div class="abs bar bar-a"></div>
    <p class="abs claim">RELIEF OF<br><strong>ANXIETY</strong> AND <strong>STRESS</strong></p>
    <div class="abs bar bar-b"></div>
    <p class="abs tagline">Vitamins · Minerals · Herbs</p>

    <div class="abs facts">SUPPLEMENT FACTS</div>
    <p class="abs ingredients lines"><b>INGREDIENTS:</b> Lorem ipsum dolor sit amet,<br>consectetuer adipiscing elit, sed diam</p>
    <p class="abs maker lines"><b>MANUFACTIRE:</b><br>VORNA HEALTH SCIENCES</p>
    <div class="abs code-box">BARCODE</div>

    <div class="abs band">
      <span class="abs band-url band-left">www.vornahealthsciences.com</span>
      <span class="abs band-center">60 CAPSULES | DIETARY SUPPLEMENT</span>
      <span class="abs band-url band-right">www.vornahealthsciences.com</span>
    </div>
  </section>
</div>
</body>
</html>
```